Commercial and Residential Paint Contractor needs website

We need a website for our residential painting, multi-family painting and commercial painting company. We paint interior and exterior of houses, apartments and commercial buildings. I would like an about us page, residential page, multi family page, commercial page and contact us. Need keywords added to website for seo opitimazation. I like this website https://www.wallcraftcrew.com/

Target Market(s)

General Contractors and commercial property managers

Coding

Coded - Design and coding required

Number of Pages Required

5+ page

Font styles to use
Sans Serif

Requirements
Must have
• I need SEO keywords on pages

```html
<!DOCTYPE html>
<html lang="en">
<head>
<meta charset="utf-8">
<title>Brightline Painting – Residential, Multi-family &amp; Commercial Painting</title>
<link href="https://fonts.googleapis.com/css2?family=Nunito:wght@300;400;600;700&display=swap" rel="stylesheet">
<style>
:root{
  --navy:#0d3a6b;
  --blue:#1457a8;
  --blue-soft:#8fb0dc;
  --red:#e02424;
  --ink:#2a2f38;
  --muted:#5a6270;
  --light:#f3f6fb;
  --white:#ffffff;
  --dark:#222222;
  --link:#2f6fd1;
}
*{box-sizing:border-box;margin:0;padding:0}
html,body{width:1200px;height:2451px;overflow:hidden}
body{font-family:'Nunito',sans-serif;color:var(--ink);background:var(--white)}
.page{position:relative;width:1200px;height:2451px;overflow:hidden}
.abs{position:absolute}

/* hero */
.hero{left:0;top:0;width:1200px;height:500px;
  background:linear-gradient(90deg,#3f6eb3 0%,#5a86c4 35%,#9cb8e0 65%,#c9d8ee 100%)}
.hero-floor{left:0;top:462px;width:1200px;height:38px;background:linear-gradient(#b7a58b,#8c7a62)}
.topbar{left:203px;top:0;width:793px;height:48px;background:rgba(255,255,255,.72)}
.brand{left:236px;top:10px;font-weight:700;font-size:22px;color:var(--blue);letter-spacing:.5px}
.phone{left:855px;top:13px;display:flex;align-items:center;gap:6px;color:var(--blue);font-size:13px}
.phone i{width:18px;height:18px;border-radius:50%;background:var(--blue);display:inline-flex;align-items:center;justify-content:center}
.navband{left:186px;top:48px;width:816px;height:42px;background:var(--navy);border-radius:6px}
.nav{left:234px;top:61px;display:flex;font-size:10px;color:var(--white)}
.nav a{color:inherit;text-decoration:none;width:100px}
.nav a.active{color:var(--red)}
.btn{display:inline-flex;align-items:center;justify-content:center;font-size:9px;text-transform:uppercase;border-radius:2px;text-decoration:none}
.btn-red{background:var(--red);color:var(--white)}
.btn-white{background:var(--white);color:var(--red)}
.btn-outline{border:1px solid var(--red);color:var(--red);background:var(--white)}
.nav-quote{left:872px;top:58px;width:93px;height:22px;font-size:7.5px}
.hero-title{left:350px;top:196px;width:500px;text-align:center;color:var(--white);font-weight:600;font-size:25px;line-height:31px}
.hero-text{left:376px;top:266px;width:448px;text-align:center;color:var(--white);font-size:9.5px;line-height:15px}
.hero-btns{left:503px;top:321px;display:flex;gap:6px}
.hero-btns .btn{height:31px;padding:0 11px}
.dots{left:589px;top:482px;display:flex;gap:4px}
.dots span{width:5px;height:5px;border-radius:50%;border:1px solid var(--white)}
.dots span:first-child{background:var(--white)}

/* headings */
.h2{width:1200px;left:0;text-align:center;font-size:25px;font-weight:600;color:var(--ink)}
.h2 .blue{color:var(--navy)} .h2 .red{color:var(--red)}

/* expertise */
.card{top:579px;width:231px;height:250px;background:var(--light)}
.card h3{font-weight:400;font-size:11px;text-align:center;margin-top:11px}
.card .photo{position:absolute;left:9px;top:35px;width:213px;height:170px}
.card .btn{position:absolute;left:9px;top:213px;width:213px;height:24px;font-size:8px}

/* reasons */
.band{left:0;width:1200px;background:var(--light)}
.reason{top:940px;width:166px;height:152px;background:var(--blue);border-radius:10px}
.reason p{position:absolute;left:0;top:88px;width:166px;text-align:center;color:var(--white);font-size:12px;line-height:15px}
.reason .ico{position:absolute;left:69px;top:48px}

/* work */
.see-more{left:0;width:1200px;top:1177px;text-align:center;font-size:8.5px;color:var(--link)}
.see-more span{text-decoration:underline}
.tile{position:absolute}

/* reviews */
.see-all{left:888px;top:1731px;font-size:8.5px;color:var(--link)}
.review{left:235px;width:730px;height:90px}
.avatar{position:absolute;left:0;top:0;width:44px;height:44px;border-radius:50%;border:2px solid var(--navy);background:#dfe6f0}
.avatar.letter{background:var(--navy);color:var(--white);display:flex;align-items:center;justify-content:center;font-size:20px}
.rname{position:absolute;left:61px;top:4px;font-size:12px}
.rdate{position:absolute;left:61px;top:20px;font-size:8px;color:var(--muted)}
.stars{position:absolute;left:196px;top:7px;font-size:12px;letter-spacing:1px;color:var(--ink)}
.score{position:absolute;left:269px;top:9px;font-size:9.5px;color:var(--muted)}
.rbody{position:absolute;left:311px;top:3px;width:419px;font-size:11.2px;line-height:16.8px;color:var(--muted)}
.rbody strong{font-weight:400;color:var(--ink);font-size:12px;display:block}
.rbody em{font-style:normal;color:var(--red);display:block}

/* footer */
.footer{left:0;top:2108px;width:1200px;height:312px;background:var(--navy);color:var(--white)}
.f-brand{left:232px;top:2320px;transform:rotate(-90deg);transform-origin:left top;font-weight:700;font-size:20px;color:var(--blue-soft);letter-spacing:1px}
.f-links a{position:absolute;left:296px;color:var(--white);text-decoration:none;font-size:11px}
.f-title{font-size:19px;font-weight:400}
.form label{position:absolute;left:421px;font-size:9px}
.form label sup{color:var(--red);font-size:8px}
.field{position:absolute;left:421px;width:295px;background:#f2f2f2;border-radius:3px;font-size:9px;color:#a0a0a0;padding:7px 6px}
.submit{left:421px;top:2356px;width:63px;height:23px;font-size:9.5px;text-transform:none}
.contact{right:235px;text-align:right;font-size:12px;line-height:18.7px;color:#dbe4f0}
.socials{right:235px;top:2277px;display:flex;gap:6px}
.socials span{width:23px;height:23px;border-radius:50%;background:var(--white)}
.copyright{left:0;top:2420px;width:1200px;height:31px;background:var(--dark);color:#bdbdbd;font-size:8px;text-align:center;line-height:31px}
</style>
</head>
<body>
<div class="page">

  <!-- hero -->
  <div class="abs hero" role="img" aria-label="Painted blue wall with a ladder, paint buckets and roller on a wooden floor"></div>
  <div class="abs hero-floor" role="img" aria-label="Wooden floor with drop cloth"></div>
  <div class="abs topbar"></div>
  <div class="abs brand">Brightline Painting</div>
  <div class="abs phone"><i><svg width="10" height="10" viewBox="0 0 24 24"><path fill="#fff" d="M6.6 10.8a15 15 0 0 0 6.6 6.6l2.2-2.2c.3-.3.7-.4 1-.2 1.1.4 2.3.6 3.6.6.6 0 1 .4 1 1V20c0 .6-.4 1-1 1A17 17 0 0 1 3 4c0-.6.4-1 1-1h3.5c.6 0 1 .4 1 1 0 1.3.2 2.5.6 3.6.1.3 0 .7-.2 1z"/></svg></i>555-318-0427</div>
  <div class="abs navband"></div>
  <nav class="abs nav">
    <a class="active" href="#">Home</a><a href="#">Services</a><a href="#">Locations</a><a href="#">About us</a><a href="#">Contact us</a>
  </nav>
  <a class="abs btn btn-red nav-quote" href="#">Get free quote</a>
  <h1 class="abs hero-title">We paint interior and exterior of houses, apartments and commercial buildings.</h1>
  <p class="abs hero-text">We are family owned and operated with over 10 years' experience. We pride our self in performing to the highest degree of workmanship standards. Our experienced estimators will meet with you and customize a proposal to meet your needs.</p>
  <div class="abs hero-btns"><a class="btn btn-white" href="#">Get free quote</a><a class="btn btn-red" href="#">Call us now</a></div>
  <div class="abs dots"><span></span><span></span><span></span></div>

  <!-- expertise -->
  <h2 class="abs h2" style="top:525px">Our expertise</h2>
  <div class="abs card" style="left:235px"><h3>Residential painting</h3>
    <div class="photo" role="img" aria-label="Freshly painted white kitchen interior" style="background:linear-gradient(#e6e3dc,#8a8378)"></div>
    <a class="btn btn-outline" href="#">Call us now</a></div>
  <div class="abs card" style="left:484px"><h3>Multi-family painting</h3>
    <div class="photo" role="img" aria-label="Apartment building facade" style="background:linear-gradient(135deg,#cdb9a1,#efe6d9)"></div>
    <a class="btn btn-red" href="#">Call us now</a></div>
  <div class="abs card" style="left:735px"><h3>Commercial painting</h3>
    <div class="photo" role="img" aria-label="Commercial gym interior with wood feature wall" style="background:linear-gradient(90deg,#6d7278,#8c6d4f,#5b5f63)"></div>
    <a class="btn btn-outline" href="#">Call us now</a></div>

  <!-- reasons -->
  <div class="abs band" style="top:861px;height:264px"></div>
  <h2 class="abs h2" style="top:879px">Reasons to choose <span class="blue">Brightline</span> <span class="red">Painting</span></h2>
  <div class="abs reason" style="left:237px"><svg class="ico" width="28" height="28" viewBox="0 0 28 28" fill="none" stroke="#fff" stroke-width="1.4"><rect x="4" y="3" width="16" height="22" rx="1"/><path d="M8 9h8M8 13h8M8 17h5"/><circle cx="21" cy="9" r="4"/></svg><p>10+ years of<br>experience</p></div>
  <div class="abs reason" style="left:424px"><svg class="ico" width="28" height="28" viewBox="0 0 28 28" fill="none" stroke="#fff" stroke-width="1.4"><circle cx="8" cy="10" r="2.5"/><circle cx="20" cy="10" r="2.5"/><circle cx="14" cy="6" r="2.5"/><path d="M4 25v-8h8v8M16 25v-8h8v8M11 19v-7h6v7"/></svg><p style="top:96px">Skilled team</p></div>
  <div class="abs reason" style="left:612px"><svg class="ico" width="28" height="28" viewBox="0 0 28 28" fill="none" stroke="#fff" stroke-width="1.4"><circle cx="14" cy="15" r="10"/><path d="M14 9v6l4 3M5 5l4-2M23 5l-4-2"/></svg><p>Record of completion<br>of projects in time</p></div>
  <div class="abs reason" style="left:799px"><svg class="ico" width="28" height="28" viewBox="0 0 28 28" fill="none" stroke="#fff" stroke-width="1.4"><path d="M6 25V15h4v10zM10 16l4-6c1-1 3 0 2 2l-1 3h6c1 0 2 1 1 2l-2 7H10"/><path d="M8 5l1 2 2 .3-1.5 1.5.3 2L8 9.8 6.2 10.8l.3-2L5 7.3 7 7zM20 3l1 2 2 .3-1.5 1.5.3 2-1.8-1-1.8 1 .3-2L17 5.3 19 5z"/></svg><p>100% satisfaction<br>Guaranteed</p></div>

  <!-- recent work -->
  <h2 class="abs h2" style="top:1150px">Our recent work</h2>
  <div class="abs see-more"><span>See more</span> ⟶</div>
  <div class="tile" style="left:235px;top:1209px;width:239px;height:229px;background:linear-gradient(90deg,#7b5c3f,#a5835e,#4e4a46)" role="img" aria-label="Gym feature wall of reclaimed wood"></div>
  <div class="tile" style="left:476px;top:1209px;width:185px;height:167px;background:linear-gradient(#eceae6,#6e6a64)" role="img" aria-label="White kitchen with island"></div>
  <div class="tile" style="left:663px;top:1209px;width:302px;height:167px;background:linear-gradient(#4c8fd9 0%,#8fbff0 45%,#b39a7b 70%,#8a8f5c 100%)" role="img" aria-label="Single-storey commercial building exterior"></div>
  <div class="tile" style="left:235px;top:1440px;width:239px;height:230px;background:linear-gradient(#dcdfe3,#4a4c50 55%,#6c6e72)" role="img" aria-label="Gym interior with graphic mural wall"></div>
  <div class="tile" style="left:476px;top:1378px;width:248px;height:292px;background:linear-gradient(90deg,#e8e8e6,#c8c8c6,#5d5d5d)" role="img" aria-label="Bright entry hall with tall windows"></div>
  <div class="tile" style="left:726px;top:1378px;width:239px;height:145px;background:linear-gradient(#5b95d6,#a59177 55%,#6f8f3f)" role="img" aria-label="Office building with lawn and walkway"></div>
  <div class="tile" style="left:726px;top:1525px;width:239px;height:145px;background:linear-gradient(#eeeae3,#5d5a55 60%,#8b7a66)" role="img" aria-label="Kitchen with dark countertop and pendant lights"></div>

  <!-- reviews -->
  <div class="abs band" style="top:1708px;height:367px"></div>
  <h2 class="abs h2" style="top:1721px">Our customer reviews</h2>
  <div class="abs see-all">See all reviews ⟶</div>

  <div class="abs review" style="top:1770px">
    <div class="avatar" role="img" aria-label="Customer portrait"></div>
    <div class="rname">Daniel Reed</div><div class="rdate">14.08.2020 &nbsp;11:34 p.m.</div>
    <div class="stars">★★★★☆</div><div class="score">4.1</div>
    <p class="rbody"><strong>Maecenas blandit diam street, Melbourne</strong>Lorem ipsum dolor sit amet, consectetur adipiscing elit, sed do eiusmod tempor incididunt ut labore et dolore magna aliqua. Quis ipsum suspendisse ultrices gravida. Risus commodo viverra maecenas accumsan lacus vel facilisis...<em>Read more..</em></p>
  </div>
  <div class="abs review" style="top:1871px">
    <div class="avatar letter">B</div>
    <div class="rname">Owen</div><div class="rdate">12.08.2020 &nbsp;10:12 p.m.</div>
    <div class="stars">★★★★☆</div><div class="score">4.0</div>
    <p class="rbody"><strong>pulvinar nibh street, Sydney</strong>Lorem ipsum dolor sit amet, consectetur adipiscing elit, sed do eiusmod tempor incididunt ut labore et dolore magna aliqua. Quis ipsum suspendisse ultrices gravida. Risus commodo viverra maecenas accumsan lacus vel facilisis...<em>Read more..</em></p>
  </div>
  <div class="abs review" style="top:1972px">
    <div class="avatar" role="img" aria-label="Customer portrait"></div>
    <div class="rname">Peter Lang</div><div class="rdate">09.08.2020 &nbsp;7:54 p.m.</div>
    <div class="stars">★★★★★</div><div class="score">5.0</div>
    <p class="rbody"><strong>quis lobortis nisl street, Melbourne</strong>Lorem ipsum dolor sit amet, consectetur adipiscing elit, sed do eiusmod tempor incididunt ut labore et dolore magna aliqua. Quis ipsum suspendisse ultrices gravida. Risus commodo viverra maecenas accumsan lacus vel facilisis...<em>Read more..</em></p>
  </div>

  <!-- footer -->
  <footer class="abs footer"></footer>
  <div class="abs f-brand">Brightline</div>
  <div class="f-links">
    <a href="#" style="top:2146px">Home</a>
    <a href="#" style="top:2190px">Services</a>
    <a href="#" style="top:2234px">Locations</a>
    <a href="#" style="top:2278px">About us</a>
    <a href="#" style="top:2322px">Contact us</a>
  </div>
  <h3 class="abs f-title" style="left:421px;top:2143px;color:#fff">Message us</h3>
  <div class="form" style="color:#fff">
    <label style="top:2172px">Name<sup>*</sup></label>
    <div class="field" style="top:2189px;height:25px">Name</div>
    <label style="top:2221px">Email<sup>*</sup></label>
    <div class="field" style="top:2237px;height:25px;font-style:italic">Email</div>
    <label style="top:2269px">Message<sup>*</sup></label>
    <div class="field" style="top:2286px;height:63px">Message</div>
  </div>
  <a class="abs btn btn-red submit" href="#">Submit</a>
  <h3 class="abs f-title" style="right:235px;top:2143px;color:#fff">Contact us</h3>
  <div class="abs contact" style="top:2177px">Address:<br>Address: Harbor Lane 14B,<br>4820 AK, Oakdale<br>Email: info@brightlinepainting.com<br>Telephone: 555-318-0427</div>
  <div class="abs socials"><span></span><span></span><span></span></div>
  <div class="abs copyright">@Copyright 2020</div>

</div>
</body>
</html>
```